Business software developers new website

We need to redesign our website. Our current website is http://www.plovencast.example/index.html, which is outdated and needs a new look. We moved out from web design and have concentrated more on the back end of the systems, for example, system support and security and cloud-based applications. Our major clients include both private and government sectors. We would like to see some designs that are all in one page, simple and clean. Prefer illustrator or obstructed images instead of real-life photos. Must look futuristic yet friendly. Attached the new logo for your references and good luck.

Target Market(s)

Medium to big company for their IT or data management. Either improve or upgrade their current system.

Industry/Entity Type

Business Software

Number of Pages Required

1 page

Colors

Designer to choose colors to be used in the design.

Requirements
Must have
• Simple and clean. Individual assets must be provided in the correct size and format(png or jpeg). Prefer Goggle fonts. Even though the logo color is red, grey and black, still prefer some modern colors that go well with red. When design, must consider the possibility to convert it into responsive.
Nice to have
• White background
Should not have
• real life photos, no slider

```html
<!DOCTYPE html>
<html lang="en">
<head>
<meta charset="utf-8">
<title>Plovencast — System Support, Security and Cloud</title>
<link rel="stylesheet" href="https://fonts.googleapis.com/css2?family=Jost:wght@300;400;500&family=Roboto+Condensed:wght@300;400;700&display=swap">
<style>
:root{
  --red:#e8232d;
  --blue:#4d7cf5;
  --ink:#222222;
  --text:#555555;
  --line:#dddddd;
  --soft:#f5f5f5;
  --white:#ffffff;
  --footer:#2c2c2c;
  --footer-text:#c9c9c9;
}
*{margin:0;padding:0;box-sizing:border-box}
html,body{width:1200px;height:4096px;overflow:hidden}
body{font-family:"Jost",sans-serif;color:var(--text);background:var(--white);position:relative}
section,header,footer,.topbar{position:absolute;left:0;width:1200px}
.abs{position:absolute}
.heading{font-family:"Roboto Condensed",sans-serif;font-weight:700;color:var(--ink);font-size:31px;line-height:1}
.heading em{font-style:normal;color:var(--red)}
.heading-mark{position:absolute;height:14px}
.heading-mark::before{content:"";position:absolute;left:0;right:0;top:7px;height:1px;background:var(--line)}
.heading-mark span{position:absolute;top:2px;width:10px;height:10px;border-radius:50%;background:var(--red)}
.btn{position:absolute;display:flex;align-items:center;gap:12px;height:34px;padding:0 16px 0 14px;background:var(--red);color:var(--white);font-size:13px;font-weight:500;border-radius:0 10px 0 10px;white-space:nowrap}
.btn i{width:8px;height:8px;border-top:2px solid var(--white);border-right:2px solid var(--white);transform:rotate(45deg);display:block}
.para{font-size:14px;line-height:25.5px;text-align:justify;color:var(--text)}
.arrow{position:absolute;width:32px;height:32px;border-radius:50%;background:var(--white);box-shadow:0 2px 8px rgba(0,0,0,.15);display:flex;align-items:center;justify-content:center}
.social{display:flex;gap:8px}
.social span{width:22px;height:22px;border-radius:50%;background:var(--red);display:block}

.topbar{top:0;height:44px;background:var(--white)}
.topbar .contact{position:absolute;left:140px;top:13px;display:flex;gap:34px;font-size:13px;color:var(--ink)}
.topbar .contact div{display:flex;align-items:center;gap:9px}
.topbar .social{position:absolute;left:972px;top:11px}

.site-header{top:44px;height:82px;background:var(--soft)}
.logo{position:absolute;font-family:"Jost",sans-serif;font-weight:400;color:var(--ink);display:flex;align-items:center;gap:10px}
.logo b{width:12px;height:12px;border-radius:50%;background:var(--red);display:block}
.site-header .logo{left:140px;top:20px;font-size:36px}
.nav{position:absolute;left:728px;top:32px;display:flex;gap:28px;font-size:12.5px;color:var(--ink)}
.nav .active{color:var(--red);font-weight:500}

.hero{top:126px;height:459px;background:var(--blue)}
.hero .lead{position:absolute;left:142px;top:122px;color:var(--white);font-family:"Roboto Condensed",sans-serif}
.hero .l1{font-weight:300;font-size:34px;line-height:40px}
.hero .l2{font-weight:700;font-size:33px;line-height:42px}
.hero .l3{font-weight:700;font-size:23px;line-height:32px}
.hero .btn{left:142px;top:267px}
.hero .art{position:absolute;left:628px;top:60px;width:420px;height:350px;border-radius:50% 50% 45% 45%;background:radial-gradient(ellipse at 50% 45%,#8fb0ff 0%,#5f8bf8 55%,rgba(77,124,245,0) 72%)}

.about{top:585px;height:565px;background:var(--soft)}
.about .art{position:absolute;left:140px;top:70px;width:424px;height:424px;border-radius:50%;border:1px dashed #e8a0a5;display:flex;align-items:center;justify-content:center}
.about .art div{width:360px;height:360px;border-radius:50%;background:radial-gradient(circle,#dcecf9 0%,#cfe6f6 60%,#e4f1fa 100%)}
.about .heading{position:absolute;left:653px;top:137px}
.about .heading-mark{left:653px;top:178px;width:100px}
.about .para{position:absolute;left:655px;top:215px;width:402px}
.about .btn{left:657px;top:391px}

.clients{top:1150px;height:586px;background:var(--white)}
.clients .heading{position:absolute;left:140px;top:172px}
.clients .heading-mark{left:140px;top:212px;width:140px}
.clients .para{position:absolute;left:140px;top:245px;width:403px}
.clients .btn{left:141px;top:400px}
.client-card{position:absolute;width:155px;height:100px;background:var(--white);box-shadow:0 3px 12px rgba(0,0,0,.12);display:flex;align-items:center;justify-content:center;font-family:"Roboto Condensed",sans-serif;font-weight:700;font-size:16px;color:var(--ink);letter-spacing:1px;text-transform:uppercase}

.services{top:1736px;height:439px;background:var(--soft)}
.center-title{position:absolute;left:0;width:1200px;text-align:center}
.services .center-title{top:74px}
.services .heading-mark{left:525px;top:116px;width:150px}
.service{position:absolute;top:158px;width:190px;text-align:center}
.service .ring{width:144px;height:144px;margin:0 auto;border-radius:50%;background:var(--white);box-shadow:0 4px 14px rgba(0,0,0,.12);display:flex;align-items:center;justify-content:center}
.service .ring.active{border:4px solid var(--red)}
.service p{margin-top:22px;font-size:15.5px;line-height:20px;color:var(--ink)}

.news{top:2175px;height:625px;background:var(--white)}
.news .center-title{top:72px}
.news .heading-mark{left:522px;top:115px;width:156px}
.news-card{position:absolute;top:155px;width:288px;height:395px;border:1px solid #d8d8d8;background:var(--white)}
.news-card .photo{position:absolute;left:8px;top:8px;width:270px;height:175px}
.news-card .date{position:absolute;right:8px;top:8px;width:36px;height:40px;background:var(--red);color:var(--white);text-align:center;font-size:15px;line-height:16px;padding-top:5px;font-weight:500}
.news-card .date small{display:block;font-size:8px;line-height:10px}
.news-card h3{position:absolute;left:14px;top:202px;width:262px;font-size:15.5px;font-weight:500;line-height:21px;color:var(--ink)}
.news-card p{position:absolute;left:14px;top:252px;width:240px;font-size:12.5px;line-height:23px;color:var(--text)}
.news-card .btn{left:16px;top:333px;height:30px;font-size:12.5px}

.faq{top:2800px;height:458px;background:var(--soft)}
.faq .h-left{position:absolute;left:140px;top:69px}
.faq .m-left{left:140px;top:110px;width:80px}
.faq .h-right{position:absolute;left:635px;top:71px}
.faq .m-right{left:635px;top:112px;width:80px}
.faq .divider{position:absolute;left:600px;top:55px;height:350px;border-left:1px dashed #cfcfcf}
.acc{position:absolute;left:140px;width:425px;background:var(--white);box-shadow:0 2px 8px rgba(0,0,0,.08)}
.acc .q{height:40px;display:flex;align-items:center;justify-content:space-between;padding:0 14px;font-size:12.5px;color:var(--ink)}
.acc .q span:last-child{color:var(--red);font-size:16px}
.acc.open .q{background:var(--red);color:var(--white)}
.acc.open .q span:last-child{color:var(--white)}
.acc .a{padding:10px 14px 14px;font-size:12.5px;line-height:23px;color:var(--text);text-align:justify}
.philosophy{position:absolute;left:635px;top:165px;width:423px;height:220px;background:var(--white);box-shadow:0 4px 16px rgba(0,0,0,.08)}
.philosophy .para{position:absolute;left:20px;top:18px;width:383px}
.philosophy .btn{left:20px;top:167px;height:31px;font-size:12.5px}

.contact-form{top:3258px;height:532px;background:var(--white)}
.contact-form .center-title{top:74px}
.contact-form .heading-mark{left:492px;top:116px;width:216px}
.field{position:absolute;height:35px;border:1px solid #d6d6d6;font-size:11px;color:#777;padding:10px 14px}
.check{position:absolute;left:607px;top:219px;width:291px;height:35px;border:1px solid #d6d6d6;display:flex;align-items:center;gap:12px;padding:0 12px;font-size:11px;color:#555}
.check .box{width:20px;height:20px;border:1px solid #bbb;background:var(--white)}
.check .badge{margin-left:auto;width:22px;height:22px;border-radius:4px;background:#c8d4ee}
.contact-form .btn{left:550px;top:405px;height:34px}

.site-footer{top:3790px;height:306px;background:var(--footer);color:var(--footer-text)}
.site-footer .logo{left:140px;top:68px;font-size:30px;color:var(--white)}
.site-footer .about-text{position:absolute;left:143px;top:113px;width:210px;font-size:11.5px;line-height:21px}
.f-title{position:absolute;top:77px;font-family:"Roboto Condensed",sans-serif;font-weight:400;font-size:14.5px;color:var(--white);letter-spacing:.3px;text-transform:uppercase}
.f-title em{font-style:normal;color:var(--red)}
.f-title::after{content:"";position:absolute;left:0;top:24px;width:34px;height:2px;background:var(--red)}
.f-list{position:absolute;top:118px;font-size:11.5px;line-height:29px;list-style:none}
.f-list li{display:flex;align-items:center;gap:10px}
.f-list.plain{line-height:25px}
.newsletter{position:absolute;left:777px;top:149px;width:283px;height:30px;border-radius:15px;background:var(--white);display:flex;align-items:center;overflow:hidden}
.newsletter span{flex:1;padding-left:14px;font-size:11px;color:#888}
.newsletter b{height:30px;width:80px;background:var(--red);color:var(--white);font-weight:500;font-size:13px;display:flex;align-items:center;justify-content:center;border-radius:15px}
.site-footer .social{position:absolute;left:783px;top:196px}
.copyright{position:absolute;left:0;top:268px;width:1200px;text-align:center;font-size:12px;color:var(--footer-text)}
</style>
</head>
<body>

<div class="topbar">
  <div class="contact">
    <div>
      <svg width="20" height="20" viewBox="0 0 24 24" fill="none" stroke="#e8232d" stroke-width="1.6"><path d="M5 3h4l2 5-3 2a12 12 0 0 0 6 6l2-3 5 2v4a2 2 0 0 1-2 2A17 17 0 0 1 3 5a2 2 0 0 1 2-2z"/></svg>
      <span>+61 7 5550 0142</span>
    </div>
    <div>
      <svg width="20" height="16" viewBox="0 0 24 18" fill="none" stroke="#e8232d" stroke-width="1.6"><rect x="1" y="1" width="22" height="16" rx="1"/><path d="M1 2l11 8 11-8"/></svg>
      <span>info@plovencast.example</span>
    </div>
  </div>
  <div class="social"><span></span><span></span><span></span></div>
</div>

<header class="site-header">
  <div class="logo">plovencast.net<b></b></div>
  <nav class="nav">
    <span class="active">Home</span>
    <span>Our Services</span>
    <span>Our Clients</span>
    <span>Contact Us</span>
  </nav>
</header>

<section class="hero">
  <div class="lead">
    <div class="l1">We provide best quality</div>
    <div class="l2">Service for System Support,</div>
    <div class="l3">Security and Cloud-based applications</div>
  </div>
  <div class="btn"><i></i>Let's Get Started</div>
  <div class="art" role="img" aria-label="Illustration of three people working on laptops at a desk beneath a data cloud"></div>
</section>

<section class="about">
  <div class="art"><div role="img" aria-label="Illustration of a team presenting around a large laptop screen"></div></div>
  <h2 class="heading">ABOUT <em>US</em></h2>
  <div class="heading-mark"><span style="left:0"></span></div>
  <p class="para">We have provided web design, graphic design and application development solutions for a wide variety of industries. We are known for the quality of our work, affordable rates and our individual approach to each customer. Our company offers a wide variety of professional web solution and all this at very competitive prices!</p>
  <div class="btn"><i></i>Read More</div>
</section>

<section class="clients">
  <h2 class="heading">Our <em>Clients</em></h2>
  <div class="heading-mark"><span style="left:0"></span></div>
  <p class="para">We undertake many projects from small businesses to large corporations. We are also extremely experienced in the long term support of comprehensive web based business systems providing first class development, maintenance, data entry services and enhancements. Click here to see more details.</p>
  <div class="btn"><i></i>Read More</div>
  <div class="arrow" style="left:599px;top:313px"><svg width="10" height="10" viewBox="0 0 10 10"><path d="M7 1L3 5l4 4" fill="none" stroke="#999" stroke-width="1.6"/></svg></div>
  <div class="arrow" style="left:1054px;top:313px"><svg width="10" height="10" viewBox="0 0 10 10"><path d="M3 1l4 4-4 4" fill="none" stroke="#999" stroke-width="1.6"/></svg></div>
  <div class="client-card" style="left:680px;top:200px">Harlow Print</div>
  <div class="client-card" style="left:850px;top:220px">Oakmere</div>
  <div class="client-card" style="left:680px;top:313px">Ridgeway</div>
  <div class="client-card" style="left:850px;top:335px">Northwing</div>
</section>

<section class="services">
  <div class="center-title"><h2 class="heading">Our <em>Services</em></h2></div>
  <div class="heading-mark"><span style="left:70px"></span></div>
  <div class="arrow" style="left:77px;top:218px"><svg width="10" height="10" viewBox="0 0 10 10"><path d="M7 1L3 5l4 4" fill="none" stroke="#999" stroke-width="1.6"/></svg></div>
  <div class="arrow" style="left:1092px;top:218px"><svg width="10" height="10" viewBox="0 0 10 10"><path d="M3 1l4 4-4 4" fill="none" stroke="#999" stroke-width="1.6"/></svg></div>

  <div class="service" style="left:119px">
    <div class="ring"><svg width="66" height="66" viewBox="0 0 66 66" fill="none" stroke="#4a4a6a" stroke-width="2"><path d="M33 5l23 8v17c0 15-10 26-23 31C20 56 10 45 10 30V13z"/><path d="M33 13l15 5v12c0 10-6 18-15 22-9-4-15-12-15-22V18z" fill="#f4a3a8" stroke="none"/><path d="M24 33l7 7 12-13" stroke="#e8232d" stroke-width="3"/></svg></div>
    <p>Security &amp; Firewalls</p>
  </div>
  <div class="service" style="left:312px">
    <div class="ring"><svg width="72" height="62" viewBox="0 0 72 62" fill="none" stroke="#4a4a6a" stroke-width="2"><rect x="3" y="6" width="48" height="32" rx="2"/><path d="M20 38v10h-8M34 38v10h8M10 48h34"/><rect x="46" y="18" width="22" height="40" rx="2" fill="#f4a3a8"/><path d="M51 26h12M51 32h12M51 38h12"/><circle cx="57" cy="50" r="2"/></svg></div>
    <p>Workstation<br>Support</p>
  </div>
  <div class="service" style="left:505px">
    <div class="ring active"><svg width="56" height="66" viewBox="0 0 56 66" fill="none" stroke="#4a4a6a" stroke-width="2"><rect x="3" y="3" width="50" height="60" rx="4"/><rect x="10" y="11" width="36" height="12" rx="2" fill="#f4a3a8"/><rect x="10" y="27" width="36" height="12" rx="2" fill="#f4a3a8"/><rect x="10" y="43" width="36" height="12" rx="2" fill="#f4a3a8"/><path d="M15 17h14M15 33h14M15 49h14"/></svg></div>
    <p>Storage</p>
  </div>
  <div class="service" style="left:698px">
    <div class="ring"><svg width="70" height="66" viewBox="0 0 70 66" fill="none" stroke="#4a4a6a" stroke-width="2"><path d="M18 38a12 12 0 0 1 0-24 16 16 0 0 1 31-2 12 12 0 0 1 3 24"/><rect x="24" y="24" width="22" height="38" rx="2" fill="#f4a3a8"/><path d="M29 32h12M29 38h12M29 44h12"/><circle cx="35" cy="54" r="2"/></svg></div>
    <p>Networks &amp;<br>Databases</p>
  </div>
  <div class="service" style="left:891px">
    <div class="ring"><svg width="72" height="64" viewBox="0 0 72 64" fill="none" stroke="#4a4a6a" stroke-width="2"><path d="M18 38a13 13 0 0 1 0-26 18 18 0 0 1 34-2 14 14 0 0 1 2 28z"/><path d="M24 38v10M36 38v16M48 38v10"/><circle cx="24" cy="52" r="4" fill="#f4a3a8"/><circle cx="36" cy="58" r="4" fill="#f4a3a8"/><circle cx="48" cy="52" r="4" fill="#f4a3a8"/></svg></div>
    <p>Cloud</p>
  </div>
</section>

<section class="news">
  <div class="center-title"><h2 class="heading">Latest <em>News</em></h2></div>
  <div class="heading-mark"><span style="left:73px"></span></div>
  <div class="arrow" style="left:76px;top:349px"><svg width="10" height="10" viewBox="0 0 10 10"><path d="M7 1L3 5l4 4" fill="none" stroke="#999" stroke-width="1.6"/></svg></div>
  <div class="arrow" style="left:1092px;top:349px"><svg width="10" height="10" viewBox="0 0 10 10"><path d="M3 1l4 4-4 4" fill="none" stroke="#999" stroke-width="1.6"/></svg></div>

  <article class="news-card" style="left:140px">
    <div class="photo" role="img" aria-label="Glowing digital globe over a city skyline at night" style="background:linear-gradient(160deg,#0c2a3c 0%,#1f6d80 50%,#0a1c28 100%)"></div>
    <div class="date">21<small>NOV</small></div>
    <h3>Website: Plovencast.net launches new website.</h3>
    <p>Our work is based on quality sales, customer and technical support services.</p>
    <div class="btn"><i></i>Read More</div>
  </article>
  <article class="news-card" style="left:456px">
    <div class="photo" role="img" aria-label="Padlock on a laptop screen with streaks of light" style="background:linear-gradient(150deg,#1b2f6b 0%,#c2364a 45%,#f1a04a 60%,#2d5aa8 100%)"></div>
    <div class="date">21<small>NOV</small></div>
    <h3>Website: Plovencast.net launches new website.</h3>
    <p>Our work is based on quality sales, customer and technical support services.</p>
    <div class="btn"><i></i>Read More</div>
  </article>
  <article class="news-card" style="left:771px">
    <div class="photo" role="img" aria-label="Businessman drawing on a virtual data chart screen" style="background:linear-gradient(120deg,#d7e6ee 0%,#a9c3d2 50%,#2c3440 100%)"></div>
    <div class="date">21<small>NOV</small></div>
    <h3>Website: Plovencast.net launches new website.</h3>
    <p>Our work is based on quality sales, customer and technical support services.</p>
    <div class="btn"><i></i>Read More</div>
  </article>
</section>

<section class="faq">
  <h2 class="heading h-left">Frequently <em>Asked Questions</em></h2>
  <div class="heading-mark m-left"><span style="left:0"></span></div>
  <div class="divider"></div>
  <div class="acc open" style="top:170px">
    <div class="q"><span>How much does a web site powered by Plovencast.net cost?</span><span>–</span></div>
    <div class="a">There are quite a few factors that are going to affect the ultimate cost of your web site. These factors include how many pages you are going to have, if you will sell products on your website, the graphic work involved, and how interactive your web site will be.</div>
  </div>
  <div class="acc" style="top:340px">
    <div class="q"><span>How long does it take to have a web site designed?</span><span>+</span></div>
  </div>

  <h2 class="heading h-right">Our <em>Philosophy</em></h2>
  <div class="heading-mark m-right"><span style="left:0"></span></div>
  <div class="philosophy">
    <p class="para">As web developers, we understand that a powerful and functional web site is a vital component of modern day marketing for companies of today. This is why our web site development team work with all of our clients to ensure their web site design will deliver to their target market.</p>
    <div class="btn"><i></i>Read More</div>
  </div>
</section>

<section class="contact-form">
  <div class="center-title"><h2 class="heading">Quick <em>Contact</em></h2></div>
  <div class="heading-mark"><span style="left:103px"></span></div>
  <div class="field" style="left:302px;top:167px;width:290px">First Name*</div>
  <div class="field" style="left:607px;top:167px;width:291px">Last Name*</div>
  <div class="field" style="left:302px;top:219px;width:290px">Email*</div>
  <div class="check"><span class="box"></span><span>I am not a robot</span><span class="badge"></span></div>
  <div class="field" style="left:302px;top:274px;width:596px;height:86px">Message*</div>
  <div class="btn"><i></i>Submit</div>
</section>

<footer class="site-footer">
  <div class="logo">plovencast.net<b></b></div>
  <p class="about-text">Plovencast.net is an Australian based Software and Web Development Company that provides individual technology solutions and professional software for clients worldwide.</p>

  <h4 class="f-title" style="left:410px">Contact <em>Details</em></h4>
  <ul class="f-list" style="left:412px">
    <li><svg width="12" height="12" viewBox="0 0 24 24" fill="#e8232d"><path d="M5 3h4l2 5-3 2a12 12 0 0 0 6 6l2-3 5 2v4a2 2 0 0 1-2 2A17 17 0 0 1 3 5a2 2 0 0 1 2-2z"/></svg>+61 7 5550 0142</li>
    <li><svg width="12" height="12" viewBox="0 0 24 24" fill="#e8232d"><rect x="6" y="1" width="12" height="22" rx="2"/></svg>+61 0400 555 018</li>
    <li><svg width="12" height="10" viewBox="0 0 24 18" fill="#e8232d"><rect x="1" y="1" width="22" height="16" rx="1"/></svg>info@plovencast.example</li>
  </ul>

  <h4 class="f-title" style="left:633px">Quick <em>Links</em></h4>
  <ul class="f-list plain" style="left:633px;top:120px">
    <li>Home</li><li>Our Services</li><li>Our Clients</li><li>Contact Us</li>
  </ul>

  <h4 class="f-title" style="left:776px">Subcribe <em>to your newletter</em></h4>
  <p class="abs" style="left:777px;top:120px;font-size:11.5px">You can be always up to date with our company news</p>
  <div class="newsletter"><span>Enter your Email*</span><b>Submit</b></div>
  <div class="social"><span></span><span></span><span></span></div>

  <p class="copyright">© 2019 plovencast. All Right Reserved.</p>
</footer>

</body>
</html>
```